San Francisco Leading Consulting firm - 47Vora Web Design Project

•Create a Web Design
•Uncoded webpage layout design
•2 Pages Design - Homepage + Interior Page

Task Description
Hello, we're looking for a re-design our current website www.47vora-example.com

we have a sample mockup design @

http://47vora.pubtrellis-example.org/

This shows the layout that we like and also a sample of 6 pictures that would change based on where you mouse over..

6 pictures HOME design needs to be included.

SMART
THOUGHTFUL
FLEXIBLE
CREATIVE SERVICES
TECHNICAL SERVICES
PARTNERS

sites we like:

http://www.melvanadvisory-example.com/Home.cfm?id=Home
http://www.plinthworks-example.com/index.html

Our company can be best described as: 100+ employees, cutting-edge, depandable, innovative, strong, smart.

Our Primary focus is: IT Consulting Services and Creative Design services

47Vora LLC is a consulting firm providing creative design, business and technology solutions to both private and public interests.

Established in 1996, 47Vora is a San Francisco based company providing specialists for a range of business needs including:

Creative Design Services
•Print
•Logo Design
•Website Design
•Illustration

and

Business and Technology solutions

•Application Software and Web Development
•Business Process Re-Design (BPR)
•Business/Systems Analysis and Requirement Documentation
•Mentoring and Training
•Network/Hardware Installation Services
•System Design and Architecture
•Vendor Management
•Docuvault Architecture and Implementation

our sample mockup site:

Reason: Due to holiday season, we're not available to work with designers and finilize our design.  

Thank you very much for submitting your design.

We appreciate your time and creativity.   Since, our office is currently closed for holidays, we will be reviewing it in details next week and will make our decision as soon as possible.

It would be great if you could submit any of your changes by Wed next week, so it would be part of our reviews. 

Please see updated wireframe under attachments:  we have some minor updates to our wireframe that we would like you to update your designs, if possible.  

We also encorouge you not to use our standard wireframe and come up with more unique designs.   Everything would be considered when we review your design.

 

Ardent Market(s)

Creative services and professional services clients, including government agencies

Industry/Entity Type

Business

Requirements
Must have
• Clean, professional look, easy navigation

```html
<!DOCTYPE html>
<html lang="en">
<head>
<meta charset="utf-8">
<title>47Vora — Creative, Business &amp; Technology Consulting</title>
<link rel="stylesheet" href="https://fonts.googleapis.com/css2?family=Arimo:wght@400;700&family=Roboto+Condensed:wght@700&display=swap">
<style>
  :root {
    --brand-blue: #0b8fc8;
    --brand-blue-deep: #0478b0;
    --brand-blue-light: #1fb0e0;
    --ink: #333333;
    --ink-soft: #555555;
    --client-grey: #6b6b6b;
    --rule: #d9d9d9;
    --card-border: #bdbdbd;
    --white: #ffffff;
  }
  * { box-sizing: border-box; margin: 0; padding: 0; }
  html, body { width: 1200px; height: 960px; overflow: hidden; background: var(--white); }
  body { position: relative; font-family: "Arimo", Arial, sans-serif; color: var(--ink); }

  /* Header */
  .site-header { position: absolute; left: 0; top: 0; width: 1200px; height: 92px; border-bottom: 2px solid var(--brand-blue); }
  .brand { position: absolute; left: 172px; top: 28px; display: flex; align-items: center; gap: 10px; }
  .brand-dot { width: 26px; height: 26px; border-radius: 50%; background: var(--brand-blue-light); }
  .brand-name { font-size: 30px; font-weight: 400; color: var(--ink-soft); letter-spacing: 1px; }
  .main-nav { position: absolute; left: 381px; top: 37px; display: flex; }
  .main-nav a { font-size: 12.5px; font-weight: 700; color: var(--ink); text-decoration: none; padding: 0 11px; line-height: 18px; border-left: 1px solid var(--brand-blue); }
  .main-nav a:first-child { border-left: 0; }
  .contact-block { position: absolute; left: 929px; top: 12px; font-size: 12px; line-height: 18px; color: #222; }
  .contact-block .accent { color: var(--brand-blue); font-weight: 700; }

  /* Hero */
  .hero { position: absolute; left: 0; top: 93px; width: 1200px; height: 527px;
    background: linear-gradient(180deg, #e6e6e6 0%, #cfcfcf 40%, #8f8f8f 75%, #6e6e6e 100%); }
  .slider { position: absolute; left: 118px; top: 44px; width: 960px; height: 349px; border-radius: 3px 3px 0 0; overflow: hidden;
    background: linear-gradient(180deg, var(--brand-blue-light) 0%, var(--brand-blue) 55%, var(--brand-blue-deep) 100%); }
  .slide-photo { position: absolute; left: 460px; top: 0; width: 410px; height: 349px;
    clip-path: polygon(0 0, 368px 0, 410px 349px, 36px 349px);
    background: linear-gradient(160deg, #f4f5f6 0%, #dfe3e6 45%, #c9ced2 100%); }
  .slide-title { position: absolute; left: 110px; top: 92px; font-family: "Roboto Condensed", "Arial Narrow", sans-serif; font-weight: 700; color: var(--white); text-shadow: 1px 2px 3px rgba(0,0,0,.3); }
  .slide-title .headline { font-size: 54px; line-height: 56px; letter-spacing: .5px; }
  .slide-title .tagline { font-size: 23px; line-height: 28px; text-transform: uppercase; }
  .slide-arrow { position: absolute; top: 157px; }
  .slide-arrow.prev { left: 20px; }
  .slide-arrow.next { right: 18px; }
  .slider-dots { position: absolute; left: 118px; top: 393px; width: 960px; height: 46px; background: rgba(255,255,255,.55); display: flex; justify-content: center; align-items: center; gap: 14px; padding-left: 4px; }
  .slider-dots span { width: 14px; height: 14px; border-radius: 50%; background: #111; }
  .slider-dots span.active { background: var(--brand-blue); }

  /* Clients */
  .clients { position: absolute; left: 120px; top: 620px; width: 960px; height: 88px; border-bottom: 1px solid var(--rule); }
  .clients-label { position: absolute; left: 6px; top: 19px; font-size: 20px; font-weight: 700; line-height: 24px; color: #222; }
  .clients-chevron { position: absolute; left: 114px; top: 24px; }
  .client-list { position: absolute; left: 160px; top: 30px; width: 800px; display: flex; justify-content: space-between; align-items: center; }
  .client { display: flex; align-items: center; gap: 5px; font-size: 15px; font-weight: 700; color: var(--client-grey); }
  .client .mark { width: 10px; height: 10px; border-radius: 50%; background: var(--client-grey); }

  /* Service cards */
  .service-card { position: absolute; top: 734px; width: 280px; height: 100px; border: 1px solid var(--card-border); border-radius: 4px; overflow: hidden; background: var(--white); }
  .service-card.creative { left: 120px; }
  .service-card.technical { left: 458px; }
  .service-card.partners { left: 793px; }
  .card-title { position: absolute; left: 6px; top: 5px; font-size: 15px; color: var(--ink-soft); }
  .card-art { position: absolute; }
  .creative .card-art { left: 80px; top: 26px; width: 148px; height: 74px; border-radius: 60px 60px 0 0; background: linear-gradient(90deg, #e25bd0, #6f7cf0, #49d3c9, #f3d64c, #ef7a5a); opacity: .8; }
  .technical .card-art { left: 46px; top: 30px; width: 160px; height: 70px; border-radius: 30px 30px 0 0; background: linear-gradient(180deg, #d8d8d8, #8a8a8a); }
  .partners .card-art { left: 88px; top: 8px; width: 140px; height: 78px; border-radius: 10px; background: linear-gradient(135deg, #f3b3d4, #a8e0f2, #c8f0a8, #f6e3a0); opacity: .85; }
  .card-corner { position: absolute; right: 0; bottom: 0; }

  /* Footer */
  .site-footer { position: absolute; left: 120px; top: 857px; width: 960px; border-top: 1px solid var(--rule); }
  .copyright { position: absolute; left: 2px; top: 17px; font-size: 12.5px; color: #333; white-space: nowrap; }
  .footer-nav { position: absolute; right: 7px; top: 18px; display: flex; gap: 30px; }
  .footer-nav a { font-size: 12.5px; font-weight: 700; color: #333; text-decoration: none; white-space: nowrap; }
</style>
</head>
<body>

<header class="site-header">
  <div class="brand"><span class="brand-dot"></span><span class="brand-name">47VORA</span></div>
  <nav class="main-nav">
    <a href="#">Company</a>
    <a href="#">Creative Services</a>
    <a href="#">Technical Services</a>
    <a href="#">Partners</a>
    <a href="#">Contact Us</a>
  </nav>
  <address class="contact-block" style="font-style:normal">
    2250 Harbor Ave, Ste 480<br>
    San Francisco, CA 94105<br>
    <span class="accent">415-555-0147</span><br>
    <span class="accent">info@47vora-example.com</span>
  </address>
</header>

<section class="hero" role="img" aria-label="Black and white aerial view of the San Francisco skyline">
  <div class="slider">
    <div class="slide-photo" role="img" aria-label="Photo of a grey-haired businessman in a light suit in a bright office"></div>
    <div class="slide-title">
      <div class="headline">THOUGHTFUL</div>
      <div class="tagline">Your project gets the<br>time it deserves</div>
    </div>
    <svg class="slide-arrow prev" width="30" height="50" viewBox="0 0 30 50" aria-hidden="true">
      <polyline points="24,3 6,25 24,47" fill="none" stroke="#fff" stroke-width="7" stroke-linejoin="miter"/>
    </svg>
    <svg class="slide-arrow next" width="30" height="50" viewBox="0 0 30 50" aria-hidden="true">
      <polyline points="6,3 24,25 6,47" fill="none" stroke="#fff" stroke-width="7" stroke-linejoin="miter"/>
    </svg>
  </div>
  <div class="slider-dots">
    <span></span><span class="active"></span><span></span><span></span><span></span><span></span>
  </div>
</section>

<section class="clients">
  <div class="clients-label">Featured<br>Clients</div>
  <svg class="clients-chevron" width="22" height="38" viewBox="0 0 22 38" aria-hidden="true">
    <polyline points="4,2 17,19 4,36" fill="none" stroke="var(--brand-blue)" stroke-width="6"/>
  </svg>
  <div class="client-list">
    <span class="client"><span class="mark"></span>Ardent</span>
    <span class="client">Lumora</span>
    <span class="client">Kestrel</span>
    <span class="client">Norvane</span>
    <span class="client">Veloxa</span>
    <span class="client">Tellwave</span>
    <span class="client">Civra</span>
    <span class="client">Fieldmark</span>
    <span class="client">Brisola</span>
  </div>
</section>

<a class="service-card creative" href="#">
  <span class="card-title">Creative Services</span>
  <div class="card-art" role="img" aria-label="Colourful abstract flowing ribbon illustration"></div>
  <svg class="card-corner" width="42" height="42" viewBox="0 0 42 42" aria-hidden="true">
    <polygon points="42,0 42,42 0,42" fill="var(--brand-blue)"/>
    <path d="M29 26v10M24 31h10" stroke="#fff" stroke-width="2.4"/>
  </svg>
</a>

<a class="service-card technical" href="#">
  <span class="card-title">Business &amp; Technical Services</span>
  <div class="card-art" role="img" aria-label="Illustration of interlocking metal gears"></div>
  <svg class="card-corner" width="42" height="42" viewBox="0 0 42 42" aria-hidden="true">
    <polygon points="42,0 42,42 0,42" fill="var(--brand-blue)"/>
    <path d="M29 26v10M24 31h10" stroke="#fff" stroke-width="2.4"/>
  </svg>
</a>

<a class="service-card partners" href="#">
  <span class="card-title">Partners</span>
  <div class="card-art" role="img" aria-label="Colourful network map of the United States"></div>
  <svg class="card-corner" width="42" height="42" viewBox="0 0 42 42" aria-hidden="true">
    <polygon points="42,0 42,42 0,42" fill="var(--brand-blue)"/>
    <path d="M29 26v10M24 31h10" stroke="#fff" stroke-width="2.4"/>
  </svg>
</a>

<footer class="site-footer">
  <p class="copyright">Copyright 2011, 47Vora, LLC All rights reserved.</p>
  <nav class="footer-nav">
    <a href="#">Home</a>
    <a href="#">Company</a>
    <a href="#">Technical Services</a>
    <a href="#">Creative Services</a>
    <a href="#">Partners</a>
    <a href="#">Contact Us</a>
  </nav>
</footer>

</body>
</html>
```